BRAMBLEFORD CONSTRUCTIONS B-Card

I currently have a b-card design but will be removing the image (tree) from the logo and have text only.
I want the card to be classy and strong within the building and construction industry.
I will be using Spot UV on the cards as per the attached examples. I will also send through some sketched ideas that I have in mind.
The color blue is similar to the image (No. 6) attached images

Target Market(s)

middle to maturre aged.
Home Owners / Renovators and Builders

Industry/Entity Type

Construction

Contact Information for Business Card

BRAMBLEFORD CONSTRUCTIONS
Name: Gareth Pennick
Title: Project Manager
Mobile: 0427 351 804
Office: (08) 9316 5172
Address: 47C Corvell Street, Harlow Vale WA 6123
Email: info@bramblefordhomes.com.au
PO Box: 3817 Harlow Vale WA 6128

Colors
0592cd
33a6d7
85cae6
1b1b1b

Requirements
Must have
• 1. It must have spot UV on the front of card, maybe back of card too
• 2. I really like the blue on image 6. (or at least a really cool electric blue against the charcoal grey background)
• 3. The font must be slimline and modern. Easy to read
• 4. There must be no black used on the card... Only greys and dark charcoal greys
• 5. Use only the text from the logo "Brambleford Constructions" Not the image of the tree. I am wanting the b-cards to be more masculine.
Nice to have
• 1. I like the design concept on image 6. but happy to see what else you can do with the Spot UV
• 2. Unless you have a really cool idea of the image of the tree (from previous logo) Spot UV somewhere in the design concept thats original and different then I am keen to see what you come up with
• 3. Try changing the color of the logo eg. full white or Blue and white
• 4. Another option is to have the Brambleford Logo on the front of card with the spot UV in the background of text which we specialise in eg, Roofing, Ceiling, Insulation, Gutter Guards, Electrical, Insurance etc and we can add or reduce items as required. Similar to image 12.
Should not have
• Do not include the image of the tree from previous logo. unless you have a really cool idea of Spot UV somewhere in the design concept thats original and different.

```html
<!DOCTYPE html>
<html lang="en">
<head>
<meta charset="utf-8">
<title>Brambleford Constructions – Business Card</title>
<link rel="stylesheet" href="https://fonts.googleapis.com/css2?family=Open+Sans:wght@300;400;600;700&display=swap">
<style>
  :root {
    --stage: #2f2a27;
    --card: #1b1b1b;
    --blue: #33a6d7;
    --blue-deep: #0592cd;
    --text: #e6e6e6;
    --silver: #d4d6d8;
    --muted: #9a9a9a;
  }
  * { box-sizing: border-box; margin: 0; padding: 0; }
  html, body {
    width: 1200px; height: 900px; overflow: hidden;
    background: var(--stage);
    font-family: "Open Sans", Arial, sans-serif;
  }
  .stage {
    position: relative; width: 1200px; height: 900px;
    display: flex; align-items: center; justify-content: center; gap: 50px;
  }
  .card {
    position: relative;
    width: 525px; height: 300px;
    background: var(--card);
    border-radius: 4px;
    box-shadow: 0 10px 30px rgba(0,0,0,.45);
  }
  /* Contact side */
  .card--contact { display: flex; align-items: center; }
  .brand-mark {
    width: 230px; height: 100%;
    display: flex; flex-direction: column; align-items: center; justify-content: center; gap: 14px;
  }
  .brand-mark__dot {
    width: 130px; height: 130px; border-radius: 50%;
    background: var(--blue);
    border: 4px solid var(--card);
    box-shadow: 0 0 0 3px var(--blue);
  }
  .brand-mark__name {
    color: var(--blue); font-size: 13px; font-weight: 600; letter-spacing: 2px;
  }
  .divider {
    width: 1px; height: 150px; background: linear-gradient(var(--blue), rgba(51,166,215,.2));
  }
  .contact { padding-left: 28px; color: var(--text); font-size: 13px; line-height: 1.35; }
  .contact__name { color: var(--blue); font-size: 17px; font-weight: 600; line-height: 1.1; }
  .contact__title { font-size: 12.5px; font-weight: 300; margin-bottom: 14px; }
  .contact__address { font-weight: 300; margin-bottom: 12px; }
  .contact__label { font-weight: 700; }
  .contact__phone { display: flex; align-items: center; gap: 8px; font-weight: 300; }
  .contact__phone svg { width: 11px; height: 13px; flex: none; }
  /* Logo side */
  .card--logo {
    display: flex; flex-direction: column; align-items: center; justify-content: center;
    color: var(--silver);
  }
  .wordmark__main { font-size: 38px; font-weight: 600; letter-spacing: 1px; line-height: 1; }
  .wordmark__sub { font-size: 15px; font-weight: 300; letter-spacing: 11px; margin-top: 10px; padding-left: 11px; }
</style>
</head>
<body>
<main class="stage">
  <section class="card card--contact" aria-label="Business card, contact side">
    <div class="brand-mark">
      <div class="brand-mark__dot" aria-hidden="true"></div>
      <span class="brand-mark__name">BRAMBLEFORD</span>
    </div>
    <div class="divider"></div>
    <div class="contact">
      <p class="contact__name">Gareth Pennick</p>
      <p class="contact__title">Project Manager</p>
      <p class="contact__address">47C Corvell Street,<br>Harlow Vale WA 6123<br><span class="contact__label">PO Box:</span> 3817 Harlow Vale WA 6128</p>
      <p class="contact__phone">
        <svg viewBox="0 0 11 13" aria-hidden="true"><rect x="2" y="0.5" width="7" height="12" rx="1.2" fill="none" stroke="var(--blue)" stroke-width="1.2"/><circle cx="5.5" cy="10.3" r=".8" fill="var(--blue)"/></svg>
        0427 351 804
      </p>
      <p class="contact__phone">
        <svg viewBox="0 0 12 12" aria-hidden="true"><path d="M2.6 0.8l2 2.2-1.1 1.5c.7 1.6 1.9 2.8 3.5 3.5l1.5-1.1 2.2 2-1.3 2C5.3 10.7 1.3 6.7.6 2.1z" fill="var(--blue)"/></svg>
        (08) 9316 5172
      </p>
    </div>
  </section>

  <section class="card card--logo" aria-label="Business card, logo side">
    <p class="wordmark__main">BRAMBLEFORD</p>
    <p class="wordmark__sub">CONSTRUCTIONS</p>
  </section>
</main>
</body>
</html>
```